Upscale neighbourhood mail campaign requiring 3 postcard designs

I am looking for a series of 3 postcards to be designed. They all must have a common look to them to show they belong to the same company. We are a local real estate company that specializes in an area called Ashvale Ridge. You can visit our website at www.ashvaleridgehomes.ca to have a peek. I have HD photos I can provide of the area, or include your own ideas/images. The post cards text will be provided and they will be sent as unaddressed admail, meaning there is no need to include areas for postage or mailing addresses. The final design should be clean, recognizable and professional. These cards must have visual impact on the recipients.

COPY for 3 POSTCARDs

POSTCARD 1

FRONT

(included Logo)

Get noticed.
Your home deserves it

BACK

We take finding Buyers for your home very seriously.

Through our unique, Ashvale Ridge specific website, targeted digital marketing, EXCLUSIVE Buyer incentives and our featured listing promotion, your home is in front of the people that want to see it. People who WANT to live in Ashvale Ridge.

Visit ashvaleridgehomes.ca to learn more about what we do so your home can GET NOTICED. Your home deserves it.

Colet Varnish- PREC | Pelham Estates LTD | 604-555-0192 | homes@varnish.ca

This communication is not intended to cause or induce breach of an existing agency agreement. Although this information has been received from sources deemed reliable, we assume no responsibility for its accuracy and without offering advice, make this submission to prior sale or lease, change in price or terms, and withdrawal without notice

POSTCARD 2

FRONT

Logo

Get noticed.
Expect the best.

BACK

You deserve the best when it comes to the marketing and exposure of your home, which is why your neighbours choose ashvaleridgehomes.ca to sell their home. Our award winning results combined with our systematized approach to marketing makes selling your home with us a breeze. In addition, you have full access to our dedicated client concierge, in place to ensure your sale is stress free and an overall rewarding experience.

Visit ashvaleridgehomes.ca to learn more about what we do so your home can GET NOTICED. Expect the best.

POSTCARD 3

FRONT

Logo

Get noticed.
Rule the web

BACK

No one promotes your home more than ashvaleridgehomes.ca. Just try us. Type ashvale ridge homes into any internet search browser and see for yourself. We advertise Ashvale Ridge internationally, in all major Canadian Cities and locally to affluent Buyers who appreciate what Ashvale Ridge has to offer. No one offers a more specific, targeted approach to getting your home sold.

Visit ashvaleridgehomes.ca to learn more about what we do so your home can GET NOTICED so you can rule the web.

Target Market(s)

Upscale neighbourhood in Surrey BC, Canada called Ashvale Ridge

Industry/Entity Type

Real Estate

Font styles to use
Other font styles liked:
• Lato

Colors

Designer to choose colors to be used in the design.

Requirements
Must have
• -Clean, impactful and professional looking card
• -Font- Lato
• -Provided Ashvale Ridge Homes logo
• -Check www.ashvaleridgehomes.ca for complimentary color scheme
• -provided Ashvale Ridge logo on the front
• -provided --CV logo, Pelham Estates logo and medallion crest on the back
• -Disclaimer in small, low-key font/color - "This communication is not intended to cause or induce breach of an existing agency agreement. Although this information has been received from sources deemed reliable, we assume no responsibility for its accuracy and without offering advice, make this submission to prior sale or lease, change in price or terms, and withdrawal without notice"
Nice to have
• -bold images, not 100% necessary though (discretion of designer)
• -impactful front of postcard
Should not have
• -cartoon style drawings
• -areas for postage or mailing addresses (this will be sent as non addressed admail by the local postal courier)

```html
<!DOCTYPE html>
<html lang="en">
<head>
<meta charset="utf-8">
<title>Ashvale Ridge Homes – Postcard 1</title>
<link rel="stylesheet" href="https://fonts.googleapis.com/css2?family=Lato:ital,wght@0,300;0,400;0,700;0,900;1,300&display=swap">
<style>
  :root{
    --gold:#a99557;
    --gold-soft:rgba(169,149,87,.82);
    --charcoal:#262729;
    --slate-glass:rgba(72,74,78,.78);
    --quote-grey:#d6d6d6;
    --paper:#ffffff;
    --stage:#e9e9e7;
    --muted:#b9b9b9;
    --ink:#2b2b2b;
    --navy:#22356b;
  }
  *{box-sizing:border-box;margin:0;padding:0}
  html,body{width:867px;height:1200px;overflow:hidden}
  body{background:var(--stage);font-family:"Lato",Arial,sans-serif;position:relative}

  .postcard{position:absolute;left:40px;width:787px;height:505px;overflow:hidden;box-shadow:0 3px 10px rgba(0,0,0,.18)}
  .postcard--front{top:60px;background:var(--charcoal)}
  .postcard--back{top:635px;background:var(--paper)}

  /* front */
  .hero{position:absolute;left:0;top:0;width:787px;height:372px;
    background:linear-gradient(180deg,#a9c4e4 0%,#c9daea 30%,#8d8f96 48%,#7c8a5e 62%,#6f9a3f 80%,#5d8a34 100%)}
  .hero__title{position:absolute;left:37px;top:70px;width:268px;height:72px;background:var(--slate-glass);
    color:#fff;font-weight:900;font-size:35px;line-height:72px;padding-left:16px;letter-spacing:.2px}
  .hero__tagline{position:absolute;left:37px;top:154px;width:364px;height:72px;background:var(--gold-soft);
    color:#f3f0e6;font-weight:300;font-size:34px;line-height:72px;padding-left:16px;letter-spacing:.3px}
  .hero__url{position:absolute;right:0;top:318px;width:250px;height:54px}
  .hero__url svg{position:absolute;inset:0}
  .hero__url span{position:absolute;right:22px;top:0;line-height:54px;color:#fff;font-style:italic;font-weight:300;font-size:21px}

  .front-band{position:absolute;left:0;top:372px;width:787px;height:133px}
  .brand{position:absolute;color:#fff;text-align:center;font-weight:400;letter-spacing:1px}
  .front-band .brand{left:30px;top:74px;width:210px}
  .brand__name{font-size:21px;line-height:24px}
  .brand__sub{font-size:11px;letter-spacing:4px;line-height:16px}
  .front-band__copy{position:absolute;left:285px;top:30px;width:460px}
  .front-band__heading{color:var(--gold);font-weight:700;font-size:17px;line-height:22px;margin-bottom:4px}
  .front-band__body{color:var(--muted);font-weight:300;font-size:12.5px;line-height:16.5px}

  /* back */
  .back-shape{position:absolute;inset:0}
  .back-heading{position:absolute;left:24px;top:32px;color:var(--gold);font-weight:700;font-size:33px;line-height:37px;letter-spacing:-.3px}
  .pitch{position:absolute;left:0;top:168px;width:436px;height:337px;background:var(--charcoal);color:#fff;padding:32px 48px 0 24px}
  .pitch p{font-size:13.5px;line-height:18px;margin-bottom:18px}
  .pitch__contact{position:absolute;left:24px;top:204px;font-size:10.5px;font-weight:700;letter-spacing:-.1px}
  .disclaimer{position:absolute;left:24px;top:236px;width:393px;height:83px;border-radius:20px;background:var(--gold);
    color:#f1ede2;font-size:9.6px;line-height:13px;padding:14px 20px 0}
  .testimonial{position:absolute;left:486px;top:48px;width:268px;color:var(--ink);font-size:13px;line-height:18px;text-align:justify}
  .testimonial__mark{color:var(--gold);font-weight:900;font-size:34px;line-height:0}
  .testimonial__mark--open{position:absolute;left:-27px;top:14px}
  .testimonial__mark--close{position:relative;top:12px;margin-left:4px}
  .testimonial__author{position:absolute;right:33px;top:198px;color:var(--gold);font-size:13px;letter-spacing:.3px}
  .postcard--back .brand{left:545px;top:402px;width:200px;color:var(--ink)}
  .postcard--back .brand__name{font-size:22px}
  .affiliations{position:absolute;left:562px;top:452px;display:flex;align-items:center;gap:12px}
  .affiliations__text{color:var(--navy);font-weight:700;font-size:10px;line-height:11px;text-align:center;width:68px}
  .affiliations__seal{width:40px;height:40px;border-radius:50%;background:#1f1f1f}
  .affiliations__tile{width:52px;height:40px;background:var(--navy)}
</style>
</head>
<body>

<section class="postcard postcard--front" aria-label="Postcard front">
  <div class="hero" role="img" aria-label="Photo of a large stone-fronted family home with a landscaped lawn under a blue sky"></div>
  <div class="hero__title">GET NOTICED</div>
  <div class="hero__tagline">Your home deserves it</div>
  <div class="hero__url">
    <svg width="250" height="54" viewBox="0 0 250 54" aria-hidden="true"><polygon points="14,0 250,0 250,54 0,54" fill="#a99557" fill-opacity=".85"/></svg>
    <span>ashvaleridgehomes.ca</span>
  </div>
  <div class="front-band">
    <div class="brand">
      <div class="brand__name">ASHVALE RIDGE</div>
      <div class="brand__sub">HOMES.CA</div>
    </div>
    <div class="front-band__copy">
      <h2 class="front-band__heading">We take finding Buyers for your home very seriously</h2>
      <p class="front-band__body">Through our unique, Ashvale Ridge specific website, targeted digital marketing, EXCLUSIVE Buyer incentives and our featured listing promotion, your home is in front of the people that want to see it. People who WANT to live in Ashvale Ridge.</p>
    </div>
  </div>
</section>

<section class="postcard postcard--back" aria-label="Postcard back">
  <svg class="back-shape" width="787" height="505" viewBox="0 0 787 505" aria-hidden="true">
    <polygon points="444,0 787,0 787,318 438,238 383,168" fill="#d6d6d6"/>
  </svg>
  <h2 class="back-heading">We take finding Buyers<br>for your home<br>very seriously.</h2>

  <div class="pitch">
    <p>Through our unique, Ashvale Ridge specific website, targeted digital marketing, <b>EXCLUSIVE</b> Buyer incentives and our featured listing promotion, your home is in front of the people that want to see it. People who WANT to live in Ashvale Ridge.</p>
    <p>Visit <b>ashvaleridgehomes.ca</b> to learn more about what we do so your home can <b>GET NOTICED</b>. Your home deserves it.</p>
    <div class="pitch__contact">Colet Varnish- PREC | Pelham Estates LTD | 604-555-0192 | homes@varnish.ca</div>
    <div class="disclaimer">This communication is not intended to cause or induce breach of an existing agency agreement. Although this information has been received from sources deemed reliable, we assume no responsibility for its accuracy and without offering advice, make this submission to prior sale or lease, change in price or terms, and withdrawal without notice.</div>
  </div>

  <blockquote class="testimonial">
    <span class="testimonial__mark testimonial__mark--open">“</span>Colet Varnish is an amazing realtor, so professional and friendly. A person that you can trust. Did not rest until he helped us find the house we wanted. This is our fourth time working with Colet, and we keep on coming back for his amazing and wonderful services. Thank you for everything Colet.<span class="testimonial__mark testimonial__mark--close">”</span>
  </blockquote>
  <div class="testimonial__author">LEON MARCHETTI</div>

  <div class="brand">
    <div class="brand__name">ASHVALE RIDGE</div>
    <div class="brand__sub">HOMES.CA</div>
  </div>
  <div class="affiliations">
    <div class="affiliations__text">PELHAM ESTATES</div>
    <div class="affiliations__seal" role="img" aria-label="Real estate board award seal"></div>
    <div class="affiliations__tile" role="img" aria-label="Agent badge"></div>
  </div>
</section>

</body>
</html>
```